Advert for Services that we offer

Brimfold Haulage Ltd need an design to represent what we do in a modern way by showing an image with a brief description and the use of corporate logo the information we will proved vie a doc file and this is to be presented in a modern way. This design will be for print & web. we have done our own design and its not great i have put this in the file repository

Target Market(s)

Motor trade

Font styles to use
Sans Serif

Colors

Designer to choose colors to be used in the design.

Requirements
Must have
• Company colour scheme as per logo within the files uploaded.
• and a small boarder to isolate it from the rest of the articles.
Nice to have
• Modern font
Should not have
• Old style font

```html
<!DOCTYPE html>
<html lang="en">
<head>
<meta charset="utf-8">
<title>Product Testing &amp; Analysis – Brimfold Haulage Ltd</title>
<link rel="stylesheet" href="https://fonts.googleapis.com/css2?family=Antonio:wght@700&family=Oswald:wght@500;600;700&display=swap">
<style>
  :root {
    --brand-blue: #2a74bf;
    --frame-blue: #2f7dc4;
    --ink: #0b0b0c;
    --white: #ffffff;
    --scene-light: #eef0f3;
    --scene-mid: #dfe3e8;
    --scene-grey: #c9d0d8;
    --scene-warm: #c97a4f;
    --scene-steel: #6f9cc4;
    --scene-deep: #2c6fa8;
    --scene-shadow: #25608f;
  }
  * { margin: 0; padding: 0; box-sizing: border-box; }
  html, body { width: 1200px; height: 727px; overflow: hidden; background: var(--white); }
  .advert {
    position: relative;
    width: 1200px;
    height: 727px;
    border: 11px solid var(--frame-blue);
    overflow: hidden;
    font-family: "Oswald", "Arial Narrow", sans-serif;
  }
  .workshop-photo {
    position: absolute;
    inset: 0;
    background:
      linear-gradient(180deg, rgba(255,255,255,0) 45%, rgba(255,255,255,0) 100%),
      linear-gradient(100deg,
        var(--scene-light) 0%,
        var(--scene-mid) 30%,
        var(--scene-grey) 44%,
        #c8a995 52%,
        var(--scene-warm) 58%,
        #8f8fa0 64%,
        var(--scene-steel) 70%,
        var(--scene-deep) 80%,
        var(--scene-shadow) 100%);
  }
  .workshop-photo::after {
    content: "";
    position: absolute;
    inset: 0;
    background: linear-gradient(90deg, rgba(238,240,243,.85) 0%, rgba(238,240,243,.55) 30%, rgba(238,240,243,0) 48%);
  }
  .headline {
    position: absolute;
    left: 50px;
    top: 53px;
    color: var(--brand-blue);
    font-family: "Antonio", "Oswald", sans-serif;
    font-weight: 700;
    font-size: 74px;
    line-height: 71px;
    letter-spacing: 0.5px;
    text-transform: uppercase;
  }
  .service-list {
    position: absolute;
    left: 36px;
    top: 232px;
    list-style: none;
  }
  .service-list li {
    color: var(--ink);
    font-weight: 600;
    font-size: 40px;
    line-height: 54.5px;
  }
  .service-list li::before {
    content: "*";
    color: var(--brand-blue);
    margin-right: 12px;
  }
  .contact {
    position: absolute;
    left: 44px;
    top: 618px;
    color: var(--brand-blue);
    font-weight: 700;
    font-size: 27px;
    line-height: 34px;
  }
  .company-name {
    position: absolute;
    right: 40px;
    top: 620px;
    display: flex;
    align-items: center;
    gap: 14px;
    color: var(--white);
    font-weight: 600;
    font-size: 32px;
    letter-spacing: 1px;
    text-transform: uppercase;
  }
  .company-name .mark {
    width: 26px;
    height: 26px;
    background: var(--white);
  }
</style>
</head>
<body>
  <main class="advert">
    <div class="workshop-photo" role="img" aria-label="Technician in blue overalls and safety glasses measuring the bore of an orange cast housing with a digital dial gauge in a workshop"></div>

    <h1 class="headline">Product Testing<br>&amp; Analysis</h1>

    <ul class="service-list">
      <li>Product Analysis &amp; Report</li>
      <li>Bearing Pre-Load Testing</li>
      <li>New Product Evaluation</li>
      <li>Metallurgical Testing</li>
      <li>Bore Measurement</li>
    </ul>

    <div class="contact">
      <p class="contact-phone">Tel: 0161 555 01 92</p>
      <p class="contact-web">www.brimfold-haulage.co.uk</p>
    </div>

    <div class="company-name">
      <span class="mark"></span>
      <span>Brimfold Haulage Ltd</span>
    </div>
  </main>
</body>
</html>
```